NexaBRIDGE new era @ Hyper Digitalization

We need a Brochure that show all our product, services and consulting related to Hyper Digitalization into the industrial internet of things world.
We need a document that can be handled as a electronic brochure, this means that we need to show strong corporate presence, with strong skill of technology, and we have credentials and key sucess projects related to Manufacturing industries.
Key industries that we attend: Automotive, Chemical, Food and Beverage, Mining, Paper and Pulp, Oil and Gas, Energy Management.
We save money to our customer in 6 ways: 1) Eficiency in operation 2) Production Control 3) Hyper Digitalization of Thing Optimizing asset ussage 4) Maintenance and predictive of assets risks 5) Quality Control reducing Cost 6) Augmented Reality in operation and control
Target Market(s)
Manufacturing Industry. CEO of companies that has challenges of saving operation costs into plants of manufacturing.
Industry/Entity Type
Software
Other font styles liked:
- MONTSERRAT
Requirements
Must have
- Technology Enviroment, our logo, our expertise, simple message about what our company does and the DNA, infography of the company, cases of sucess, cases of savings $ using our tecnology and services, what we can do for the customer in a few words
Nice to have
- standarize our colors related to our presentation, futuristic, information related to Artificial Inteligence related to machinery
Should not have
- old version of technology,

```html
<!DOCTYPE html>
<html lang="en">
<head>
<meta charset="utf-8">
<title>NexaBRIDGE Brochure Pages</title>
<link href="https://fonts.googleapis.com/css2?family=Montserrat:wght@400;500;600;700;800&display=swap" rel="stylesheet">
<style>
:root{
  --board:#dcdcdc;
  --royal:#0f46b4;
  --royal-deep:#0a3596;
  --sky:#3aa6e6;
  --faded-blue:#3d6cc4;
  --brand-blue:#1a6fc4;
  --ink:#333a44;
  --ink-soft:#4a4f58;
  --grey-label:#1e1e1e;
  --teal-photo:#2f5f72;
  --teal-light:#5fb4cc;
  --themes-blue:#0f5f9e;
  --terms-dark:#262626;
  --dna-panel:#2c2f72;
  --dna-title:#4b55d0;
  --night:#15142b;
  --white:#ffffff;
}
*{margin:0;padding:0;box-sizing:border-box}
html,body{width:1200px;height:791px;overflow:hidden;background:var(--board)}
body{position:relative;font-family:"Montserrat",sans-serif;color:var(--ink)}
.page{position:absolute;width:538px;height:302px;overflow:hidden}
.page--cover{left:55px;top:52px;background:linear-gradient(110deg,var(--royal-deep) 0%,var(--royal) 55%,#1b55cc 100%)}
.page--message{left:619px;top:52px;background:var(--white)}
.page--themes{left:55px;top:416px}
.page--dna{left:619px;top:416px;background:var(--night)}
.page-label{position:absolute;font-size:14px;font-weight:400;color:var(--grey-label);letter-spacing:.2px}
.abs{position:absolute}
.brand{position:absolute;font-weight:500;white-space:nowrap;line-height:1}
.web{position:absolute;font-size:6px;letter-spacing:2.2px;white-space:nowrap}
.check{width:7px;height:7px;flex:none;margin-top:1px}
.tick-list{position:absolute;list-style:none}
.tick-list li{display:flex;gap:6px;align-items:flex-start}

/* cover */
.cover-art{position:absolute;left:0;top:0}
.cover-brand{left:26px;top:36px;font-size:25px;color:var(--sky)}
.cover-tag{left:27px;top:94px;color:var(--white);font-size:10.5px;line-height:15px}
.cover-tag strong{font-weight:700;font-size:12px}
.cover-industries{left:27px;top:146px;color:var(--white);font-size:6.6px;letter-spacing:.2px}
.cover-industries li{height:15.3px;align-items:center}
.cover-industries .check{margin-top:0}
.cover-year{position:absolute;left:26px;top:230px;font-size:32px;font-weight:800;letter-spacing:8px;color:var(--faded-blue);line-height:1}
.cover-rule{left:27px;top:267px;width:128px;height:1px;background:rgba(255,255,255,.55)}
.cover-web{left:27px;top:274px;color:var(--white);font-size:7px}

/* key message */
.message-art{position:absolute;left:0;top:0}
.message-brand{left:17px;top:20px;font-size:12.5px;color:var(--brand-blue)}
.message-title{position:absolute;left:17px;top:49px;width:240px;font-size:10.2px;line-height:14px;font-weight:700;color:var(--brand-blue)}
.message-kicker{position:absolute;left:294px;top:15px;font-size:32px;font-weight:800;color:var(--teal-light);letter-spacing:.5px;white-space:nowrap;opacity:.9}
.message-points{position:absolute;left:18px;top:126px;width:200px;list-style:none;font-size:6.1px;line-height:8px;color:var(--ink)}
.message-points li{position:relative;padding-left:11px;margin-bottom:5px}
.message-points li::before{content:"";position:absolute;left:1px;top:2.5px;width:2.5px;height:2.5px;border-radius:50%;background:var(--brand-blue)}
.message-web{left:19px;top:276px;color:var(--ink);font-size:5.5px}

/* themes */
.themes-photo{position:absolute;inset:0;background:linear-gradient(180deg,#e9d7c4 0%,#ecd0ae 35%,#d9b79c 55%,#8a7a86 70%,#5b4d68 82%,#3a3050 100%)}
.themes-brand{left:17px;top:20px;font-size:12px;color:var(--white)}
.info-box{position:absolute;top:48px;width:232px;height:123px;border:1px solid rgba(40,60,90,.55);border-radius:10px;background:rgba(246,232,210,.35);overflow:hidden}
.info-box--themes{left:25px}
.info-box--terms{left:274px}
.info-box h2{height:22px;line-height:22px;text-align:center;color:var(--white);font-size:11.5px;font-weight:700;border-radius:10px 10px 0 0}
.info-box--themes h2{background:linear-gradient(180deg,#1677b6,var(--themes-blue))}
.info-box--terms h2{background:linear-gradient(180deg,#3e3e3e,var(--terms-dark))}
.info-box .tick-list{position:static;padding:0 14px;font-size:6.3px;line-height:8.4px;color:var(--ink-soft)}
.info-box--themes .tick-list{padding-top:14px}
.info-box--themes .tick-list li{margin-bottom:9px}
.info-box--terms .tick-list{padding-top:9px}
.info-box--terms .tick-list li{margin-bottom:3.6px}
.themes-web{left:19px;top:275px;color:var(--white);font-size:5.5px}

/* dna */
.dna-photo{position:absolute;left:206px;top:0;width:332px;height:302px;background:radial-gradient(circle at 52% 15%,#5ab6d8 0%,#2a5a84 6%,#1f3d66 14%,#1a1d3e 38%,#22182e 70%,#2a1620 100%)}
.dna-edge{position:absolute;left:0;top:0;width:28px;height:302px;background:linear-gradient(180deg,#1a1a36,#141328)}
.dna-panel{position:absolute;left:28px;top:0;width:178px;height:302px;background:var(--dna-panel)}
.dna-brand{left:0;width:178px;top:20px;text-align:center;font-size:12px;color:var(--sky)}
.dna-title{position:absolute;left:0;width:178px;top:52px;text-align:center;font-size:27px;font-weight:800;color:var(--dna-title);letter-spacing:.3px;line-height:1}
.dna-text{position:absolute;left:11px;top:94px;width:157px;font-size:6.3px;line-height:8.6px;color:#e6e7f5;text-align:justify}
.dna-sub{position:absolute;left:24px;top:146px;font-size:8px;font-weight:700;color:var(--white)}
.dna-commit{left:11px;top:168px;width:150px;font-size:6.3px;line-height:8.6px;color:#e6e7f5}
.dna-commit li{margin-bottom:8.5px;gap:6px}
.dna-web{left:0;width:178px;text-align:center;top:276px;color:#e6e7f5;font-size:5.5px}
</style>
</head>
<body>

<svg width="0" height="0" style="position:absolute" aria-hidden="true">
  <symbol id="tick" viewBox="0 0 10 10">
    <path d="M8.6 3.6A4 4 0 1 1 6.8 1.4" fill="none" stroke="currentColor" stroke-width="1"/>
    <path d="M3 4.8l2 2L9.2 2" fill="none" stroke="currentColor" stroke-width="1.1"/>
  </symbol>
</svg>

<!-- Cover -->
<section class="page page--cover">
  <svg class="cover-art" width="538" height="302" viewBox="0 0 538 302">
    <defs>
      <clipPath id="coverLens"><circle cx="502" cy="150" r="268"/></clipPath>
      <linearGradient id="showroom" x1="0" y1="0" x2="1" y2="1"><stop offset="0" stop-color="#9aa6b8"/><stop offset="1" stop-color="#3b4658"/></linearGradient>
      <linearGradient id="driving" x1="0" y1="0" x2="0" y2="1"><stop offset="0" stop-color="#c9a7c4"/><stop offset=".4" stop-color="#7a5c6e"/><stop offset="1" stop-color="#2c2a34"/></linearGradient>
      <linearGradient id="bottling" x1="0" y1="0" x2="0" y2="1"><stop offset="0" stop-color="#c8ccd2"/><stop offset="1" stop-color="#5a6068"/></linearGradient>
      <radialGradient id="globe" cx=".35" cy=".55" r=".6"><stop offset="0" stop-color="#3a72c0"/><stop offset=".6" stop-color="#1d4a8e"/><stop offset="1" stop-color="#0d2a5a"/></radialGradient>
    </defs>
    <g clip-path="url(#coverLens)">
      <rect x="220" y="0" width="318" height="87" fill="url(#showroom)" role="img" aria-label="Photo of cars in a showroom"/>
      <rect x="220" y="89" width="318" height="116" fill="url(#driving)" role="img" aria-label="Photo of hands on a steering wheel"/>
      <rect x="220" y="207" width="318" height="95" fill="url(#bottling)" role="img" aria-label="Photo of a bottling line"/>
    </g>
    <circle cx="502" cy="150" r="268" fill="none" stroke="#ffffff" stroke-width="2"/>
    <circle cx="623" cy="150" r="287" fill="#0d2a5a"/>
    <circle cx="623" cy="150" r="283" fill="url(#globe)" role="img" aria-label="Night view of Earth with connection lines"/>
  </svg>
  <span class="brand cover-brand">NexaBRIDGE</span>
  <p class="abs cover-tag">WE HAVE A SOLUTION FOR<br><strong>ALL TYPES OF INDUSTRY.</strong></p>
  <ul class="tick-list cover-industries">
    <li><svg class="check"><use href="#tick" style="color:#cfe0ff"/></svg>AUTOMOTIVE, CHEMICAL</li>
    <li><svg class="check"><use href="#tick" style="color:#cfe0ff"/></svg>FOOD AND BEVERAGE</li>
    <li><svg class="check"><use href="#tick" style="color:#cfe0ff"/></svg>MINING, PAPER AND PULP,</li>
    <li><svg class="check"><use href="#tick" style="color:#cfe0ff"/></svg>OIL AND GAS, ENERGY MANAGEMENT</li>
  </ul>
  <div class="cover-year">2021</div>
  <div class="abs cover-rule"></div>
  <span class="web cover-web">www.nexabridge-mx.com</span>
</section>
<div class="page-label" style="left:55px;top:366px">PAGE 1</div>

<!-- Key message -->
<section class="page page--message">
  <svg class="message-art" width="538" height="302" viewBox="0 0 538 302">
    <defs>
      <linearGradient id="city" x1="0" y1="0" x2="0" y2="1"><stop offset="0" stop-color="#5a8a9c"/><stop offset=".4" stop-color="#2f5f72"/><stop offset="1" stop-color="#173645"/></linearGradient>
      <linearGradient id="paper" x1="0" y1="0" x2="1" y2="1"><stop offset="0" stop-color="#ffffff"/><stop offset=".6" stop-color="#f1f3f5"/><stop offset="1" stop-color="#ffffff"/></linearGradient>
    </defs>
    <rect width="538" height="302" fill="url(#city)" role="img" aria-label="Photo of a city skyline with skyscrapers"/>
    <polygon points="0,0 245,0 306,165 210,302 0,302" fill="url(#paper)"/>
    <polygon points="304,140 284,183 327,183" fill="none" stroke="#ffffff" stroke-width="3"/>
    <polygon points="357,250 326,302 382,302" fill="#ffffff"/>
    <polygon points="350,262 332,302 338,302 354,268" fill="#2f5f72"/>
  </svg>
  <div class="message-kicker">KEY MESSAGE</div>
  <span class="brand message-brand">NexaBRIDGE</span>
  <h1 class="message-title">Brochure to be delivered by our marketing process &amp; sales, This brochure will be deliverted to CEO´s worldwide in Industrial companies.</h1>
  <ul class="message-points">
    <li>Need to show in a few pages, what we can do for them:</li>
    <li>We offer product and projects to transform operations in manufacturing.</li>
    <li>Our work drives customers to Competitive Advantage Mode.</li>
    <li>We use Artificial Intelligence, Hyper Digitalization and Machine Learning</li>
    <li>Techniques to obtain cost reduction in Production Process, Better Quality Delivery,</li>
    <li>Asset &amp; Optimization Performance.</li>
    <li>We add productivity without changes into their actual operations in assetts</li>
  </ul>
  <span class="web message-web">www.nexabridge-mx.com</span>
</section>
<div class="page-label" style="left:629px;top:366px">PAGE 2</div>

<!-- Themes -->
<section class="page page--themes">
  <div class="themes-photo" role="img" aria-label="Photo of a container port and city skyline at sunset"></div>
  <span class="brand themes-brand">NexaBRIDGE</span>
  <div class="info-box info-box--themes">
    <h2>THEMES</h2>
    <ul class="tick-list">
      <li><svg class="check"><use href="#tick" style="color:#3a3f48"/></svg>We offer high performance technology</li>
      <li><svg class="check"><use href="#tick" style="color:#3a3f48"/></svg>State of the art in techniques with Artificial Intelligence and prototypes for new ways of doing manufacturing</li>
      <li><svg class="check"><use href="#tick" style="color:#3a3f48"/></svg>We play the rol as an Architect for a Digital world into the shopfloor operation at Machine Levels</li>
    </ul>
  </div>
  <div class="info-box info-box--terms">
    <h2>TERMS &amp; BENEFITS</h2>
    <ul class="tick-list">
      <li><svg class="check"><use href="#tick" style="color:#3a3f48"/></svg>Reduce cost operation in manufacturing in 30%</li>
      <li><svg class="check"><use href="#tick" style="color:#3a3f48"/></svg>Augmented Reality functions, adds 60% of productivity and efficiency at operator levels</li>
      <li><svg class="check"><use href="#tick" style="color:#3a3f48"/></svg>Save 17% in Energy for production</li>
      <li><svg class="check"><use href="#tick" style="color:#3a3f48"/></svg>Zero Unplanned Downtime in machine level</li>
      <li><svg class="check"><use href="#tick" style="color:#3a3f48"/></svg>Optimize consistency in recipes by 10% delivers 32% of cost reduction</li>
      <li><svg class="check"><use href="#tick" style="color:#3a3f48"/></svg>Supply Chain optimization by 1% of the cost of goods</li>
    </ul>
  </div>
  <span class="web themes-web">www.nexabridge-mx.com</span>
</section>
<div class="page-label" style="left:55px;top:735px">PAGE 3</div>

<!-- DNA -->
<section class="page page--dna">
  <div class="dna-photo" role="img" aria-label="Illustration of a hand touching a glowing DNA strand in space"></div>
  <div class="dna-edge"></div>
  <div class="dna-panel">
    <span class="brand dna-brand">NexaBRIDGE</span>
    <h2 class="dna-title">OUR DNA</h2>
    <p class="dna-text">We want all companies to operate in an automated way, to be more efficient an dto compate with whoever is globally. We have the knwledge and experience to achive it.</p>
    <h3 class="dna-sub">Our Commitments:</h3>
    <ul class="tick-list dna-commit">
      <li><svg class="check"><use href="#tick" style="color:#b9bce0"/></svg>Improve the operation of each company individually.</li>
      <li><svg class="check"><use href="#tick" style="color:#b9bce0"/></svg>Impact the country's competitiveness</li>
      <li><svg class="check"><use href="#tick" style="color:#b9bce0"/></svg>Support Companies to access the highest levels of development, productivity, financing and profitability.</li>
    </ul>
    <span class="web dna-web">www.nexabridge-mx.com</span>
  </div>
</section>
<div class="page-label" style="left:629px;top:735px">PAGE 4</div>

</body>
</html>
```